Zvo Klinieken website for a maxillofacial surgery clinic

It's a website for a clinic for maxillofacial surgery in WordPress . The website doesn't need to be complicated but has to look professional. It needs to be in Dutch so i can give the texts. Similar websites are www.tandartsenpraktijkveldorm.nl or www.pbtspecialisten.nl. Pages would be sort of similar to https://hetcentrumvoorgezichtszorg.nl/ or https://wervelmondclinics.nl/. Those lasts are maxillofacial surgery clinic websites, but there are little more extensive.
I uploaded the logo. If this is not the proper quality i can upload the eps. Logo was made through pixelforum.

Target Market(s)

Patients who can find me and see information about the clinic

Industry/Entity Type

Healthcare

Coding

Coded - Design and coding required

Number of Pages Required

5+ page

Font styles to use
Other font styles liked:
• Something standard professional

Colors
0054AA
0677BA
7BADD7
CADEEF
E8F1F8

Requirements
Nice to have
• Something in line with the logo. I prefer a little dark like the darker logos but I'm not sure if that's professional. Logos bkvzo and rlpw are instances i'm registered to so they will have to be on the website too but small somewhere.

```html
<!DOCTYPE html>
<html lang="nl">
<head>
<meta charset="utf-8">
<title>Zvo Klinieken Zoetermeer</title>
<link href="https://fonts.googleapis.com/css2?family=Montserrat:wght@400;500;600;700;800&family=Roboto:wght@400;500;700&display=swap" rel="stylesheet">
<style>
:root{
  --blue:#29a3df;
  --blue-dark:#1d8cc8;
  --ink:#1d1d1f;
  --text:#4a4a4a;
  --muted:#8a8f98;
  --nav:#5d6673;
  --slate:#6f87ab;
  --slate-ring:#5b6f8f;
  --grey-bg:#f4f5f7;
  --footer:#1b1c1e;
  --white:#ffffff;
  --star:#f5a623;
}
*{margin:0;padding:0;box-sizing:border-box}
html,body{width:1200px;height:3928px;overflow:hidden}
body{position:relative;background:var(--white);font-family:'Roboto',sans-serif;color:var(--text)}
.abs{position:absolute}
.btn{position:absolute;display:flex;align-items:center;justify-content:center;gap:8px;background:var(--blue);color:var(--white);border-radius:30px;font-family:'Roboto',sans-serif;font-weight:700;font-size:13px;letter-spacing:.2px;text-transform:uppercase}
.btn .arrow{width:12px;height:12px}
.h2{position:absolute;left:0;width:1200px;text-align:center;font-family:'Montserrat',sans-serif;font-size:40px;color:var(--ink);letter-spacing:1px}
.h2 b{font-weight:800}
.h2 span{font-weight:400}
.divider{position:absolute;left:535px;width:130px;height:20px}

/* header */
.logo-name{font-family:'Montserrat',sans-serif;font-weight:700;color:var(--blue);font-size:30px;display:flex;align-items:center;gap:10px}
.logo-dot{width:22px;height:22px;border-radius:50%;background:var(--blue)}
.call-label{font-size:10px;font-weight:500;color:var(--nav);text-transform:uppercase}
.call-number{font-size:22px;font-weight:700;color:var(--blue);letter-spacing:.5px}
.nav a{position:absolute;top:120px;font-family:'Montserrat',sans-serif;font-weight:500;font-size:15px;color:var(--nav);text-decoration:none;letter-spacing:.3px}
.nav a.active{color:var(--blue)}

/* hero */
.hero{position:absolute;left:0;top:159px;width:1200px;height:677px;overflow:hidden;background:linear-gradient(100deg,#dfe4ea 0%,#cfd7e0 45%,#b9c7d6 70%,#9fb3c8 100%)}
.hero-title{left:110px;top:180px;font-family:'Montserrat',sans-serif;font-size:48px;line-height:56px;color:#1f2328}
.hero-title b{font-weight:800}
.hero-title span{font-weight:400}
.hero-text{left:110px;top:302px;width:450px;font-size:20px;line-height:31px;color:#333}
.dot{position:absolute;left:1139px;width:7px;height:7px;border-radius:50%;background:var(--white)}

/* treatments */
.card{position:absolute;width:230px;height:281px;border:4px solid var(--white);border-radius:6px;box-shadow:0 6px 18px rgba(0,0,0,.16);overflow:hidden}
.card .photo{position:absolute;inset:0}
.card .label{position:absolute;left:0;right:0;bottom:22px;text-align:center;color:var(--white);font-weight:700;font-size:16px;text-shadow:0 1px 3px rgba(0,0,0,.4)}

/* about */
.about-text{left:618px;width:471px;font-size:14.5px;line-height:26px;color:var(--white);text-align:justify}

/* testimonials */
.t-card{position:absolute;top:2527px;width:305px;height:320px;background:var(--white);border-top:4px solid var(--slate-ring);border-radius:8px;box-shadow:0 8px 24px rgba(0,0,0,.06);text-align:center}
.t-avatar{position:absolute;left:106px;top:-50px;width:92px;height:92px;border-radius:50%;border:4px solid var(--slate-ring);background:linear-gradient(160deg,#e8ecf1,#b5c0cd)}
.t-name{position:absolute;top:70px;left:0;right:0;font-weight:500;font-size:16px;color:var(--ink);text-transform:uppercase}
.t-stars{position:absolute;top:96px;left:0;right:0;color:var(--star);font-size:12px;letter-spacing:2px}
.t-text{position:absolute;top:126px;left:22px;right:22px;font-size:15px;line-height:26px;color:var(--text)}
.t-arrow{position:absolute;top:2661px;width:34px;height:34px;border-radius:50%}

/* contact */
.field{position:absolute;background:var(--white);box-shadow:0 3px 14px rgba(0,0,0,.09);font-size:14px;color:var(--muted);padding:16px 18px}

/* footer */
.footer-base{position:absolute;left:0;top:3600px;width:1200px;height:328px;background:var(--footer)}
.f-head{position:absolute;top:3609px;font-family:'Roboto',sans-serif;font-weight:700;font-size:16px;color:var(--white);text-transform:uppercase}
.f-line{position:absolute;top:3637px;width:32px;height:3px;background:var(--blue)}
.f-item{position:absolute;font-size:13.5px;color:#e6e6e6;display:flex;align-items:center;gap:14px}
.f-item i{display:block;width:11px;height:11px;border-radius:50%;background:var(--blue);position:relative}
.f-item i::after{content:"";position:absolute;left:3px;top:3px;width:3px;height:3px;border-top:1.5px solid var(--footer);border-right:1.5px solid var(--footer);transform:rotate(45deg)}
.f-contact{position:absolute;left:875px;font-size:13.5px;line-height:21px;color:#e6e6e6}
.f-contact b{color:var(--white);font-weight:700}
.f-icon{position:absolute;left:853px}
.social{position:absolute;top:3881px;width:32px;height:32px;border-radius:50%;border:1.5px solid var(--white)}
</style>
</head>
<body>

<!-- Header -->
<header>
  <div class="abs logo-name" style="left:111px;top:60px"><span class="logo-dot"></span>Zvo Klinieken</div>
  <div class="btn" style="left:613px;top:26px;width:209px;height:46px">Maak een afspraak
    <svg class="arrow" viewBox="0 0 12 12"><circle cx="6" cy="6" r="6" fill="#fff"/><path d="M5 3.5 7.5 6 5 8.5" stroke="#29a3df" stroke-width="1.6" fill="none"/></svg>
  </div>
  <svg class="abs" style="left:840px;top:22px" width="48" height="48" viewBox="0 0 48 48">
    <circle cx="24" cy="24" r="22.5" fill="none" stroke="#c9d3de" stroke-width="1.5"/>
    <path d="M17 15c1-1 2.5-1 3 0l2 4c.4.8 0 1.7-.6 2.2l-1.4 1c1 2.5 3 4.5 5.5 5.6l1-1.4c.6-.7 1.5-.9 2.2-.5l4 2c1 .5 1 2 0 3l-1.6 1.6c-1.4 1.4-3.6 1.6-5.4.6-4.6-2.4-8.2-6-10.5-10.6-.9-1.8-.7-4 .7-5.4z" fill="#5d6673"/>
    <path d="M27 16a6 6 0 0 1 5 5M27 12a10 10 0 0 1 9 9" stroke="#5d6673" stroke-width="1.5" fill="none"/>
  </svg>
  <div class="abs call-label" style="left:904px;top:28px">Bel voor een afspraak:</div>
  <div class="abs call-number" style="left:904px;top:44px">+31 (79) 555 0142</div>
  <nav class="nav">
    <div class="abs" style="left:491px;top:99px;width:50px;height:3px;background:#29a3df"></div>
    <a class="active" style="left:491px">HOME</a>
    <a style="left:575px">OVER ONS</a>
    <a style="left:694px">BEHANDELINGEN</a>
    <a style="left:871px">DE PRAKTIJK</a>
    <a style="left:1011px">CONTACT</a>
  </nav>
</header>

<!-- Hero -->
<section class="hero">
  <div class="abs" style="left:540px;top:0;width:660px;height:677px;background:radial-gradient(ellipse at 50% 45%,#c9b8a8 0%,#9fb6cc 38%,rgba(159,179,200,0) 70%)" role="img" aria-label="Photo of a smiling dentist in blue scrubs with arms crossed in a bright clinic"></div>
  <h1 class="abs hero-title"><b>ZVO KLINIEKEN</b><br><span>ZOETERMEER</span></h1>
  <p class="abs hero-text">Lorem ipsum dolor sit amet, consectetur adipis elit sed do eiusmod tempea.</p>
  <div class="btn" style="left:110px;top:390px;width:209px;height:47px">Maak een afspraak
    <svg class="arrow" viewBox="0 0 12 12"><circle cx="6" cy="6" r="6" fill="#fff"/><path d="M5 3.5 7.5 6 5 8.5" stroke="#29a3df" stroke-width="1.6" fill="none"/></svg>
  </div>
  <span class="dot" style="top:208px"></span>
  <span class="abs" style="left:1130px;top:233px;width:25px;height:25px;border-radius:50%;background:#fff"></span>
  <span class="abs" style="left:1139px;top:242px;width:7px;height:7px;border-radius:50%;background:#29a3df"></span>
  <span class="dot" style="top:274px"></span>
  <span class="dot" style="top:297px"></span>
  <span class="abs" style="left:1142px;top:326px;width:1.5px;height:67px;background:#fff"></span>
  <svg class="abs" style="left:0;top:0" width="1200" height="677" viewBox="0 0 1200 677">
    <path d="M0 558C140 650 290 690 430 677L0 677Z" fill="#fff"/>
    <path d="M380 677C650 640 880 510 1080 522C1140 526 1175 538 1200 552L1200 634C960 606 700 660 430 677Z" fill="#29a3df"/>
    <path d="M430 677C700 660 960 606 1200 634L1200 677Z" fill="#fff"/>
  </svg>
</section>

<!-- Treatments -->
<section>
  <h2 class="h2" style="top:908px"><b>ONZE</b> <span>BEHANDELINGEN</span></h2>
  <svg class="divider" style="top:960px" viewBox="0 0 130 20"><path d="M0 10H57M73 10H130" stroke="#6f87ab" stroke-width="1.5"/><circle cx="65" cy="10" r="7" fill="none" stroke="#6f87ab" stroke-width="1.5"/><circle cx="65" cy="10" r="2.5" fill="#29a3df"/></svg>
  <p class="abs" style="left:160px;top:998px;width:880px;text-align:center;font-size:15px;line-height:27px;color:#333">Lorem ipsum dolor sit amet, consectetur adipiscing elit, sed do eiusmod tempor incididunt ut labore et dolore magna aliqua ut enim ad minim veniam, quis nostrud exercitation ullamco.</p>

  <div class="card" style="left:111px;top:1086px"><div class="photo" role="img" aria-label="Photo of a practitioner treating a patient's face" style="background:linear-gradient(170deg,#e9e4df,#c7b6a6 55%,#8f8a86)"></div><div class="label">LOREM IPSUM</div></div>
  <div class="card" style="left:361px;top:1128px"><div class="photo" role="img" aria-label="Photo of a masked practitioner performing a facial treatment" style="background:linear-gradient(170deg,#f1f1f1,#d6cbc1 55%,#8e8882)"></div><div class="label">LOREM IPSUM</div></div>
  <div class="card" style="left:610px;top:1086px"><div class="photo" role="img" aria-label="Photo of a dentist showing an X-ray to a patient" style="background:linear-gradient(170deg,#dbe8ee,#9fc3cf 50%,#6b8796)"></div><div class="label">LOREM IPSUM</div></div>
  <div class="card" style="left:858px;top:1128px"><div class="photo" role="img" aria-label="Photo of a surgical team in an operating room" style="background:linear-gradient(170deg,#c9d9e8,#5f8fbf 55%,#2e5577)"></div><div class="label">LOREM IPSUM</div></div>

  <div class="btn" style="left:470px;top:1458px;width:260px;height:47px">Nieuw alle behandelingen
    <svg class="arrow" viewBox="0 0 12 12"><circle cx="6" cy="6" r="6" fill="#fff"/><path d="M5 3.5 7.5 6 5 8.5" stroke="#29a3df" stroke-width="1.6" fill="none"/></svg>
  </div>
</section>

<!-- Grey band behind lower about + testimonials -->
<div class="abs" style="left:0;top:2100px;width:1200px;height:828px;background:var(--grey-bg)"></div>

<!-- About -->
<section>
  <svg class="abs" style="left:0;top:1470px" width="1200" height="990" viewBox="0 1470 1200 990" role="img" aria-label="Photo of a smiling woman in a dental chair with a slate-blue overlay">
    <defs>
      <linearGradient id="aboutFill" x1="0" y1="0" x2="1" y2="0">
        <stop offset="0" stop-color="#8fa3c0"/>
        <stop offset=".35" stop-color="#7a91b3"/>
        <stop offset="1" stop-color="#667fa6"/>
      </linearGradient>
    </defs>
    <path d="M0 1746Q600 1472 1200 1746L1200 2143Q600 2453 0 2143Z" fill="url(#aboutFill)"/>
  </svg>
  <h2 class="abs" style="left:618px;top:1755px;font-family:'Montserrat',sans-serif;font-size:42px;color:#fff;letter-spacing:1px"><b style="font-weight:800">OVER</b> <span style="font-weight:400">ONS</span></h2>
  <div class="abs" style="left:618px;top:1810px;width:87px;height:3px;background:#fff"></div>
  <p class="abs about-text" style="top:1844px">Lorem ipsum dolor sit amet, consectetur adipiscing elit, sed do eiusmod tempor incididunt ut labore et dolore magna aliqua. Ut enim ad minim veniam, quis nostrud exercitation ullamco laboris nisi ut aliquip ex ea commodo consequat duis aute irure dolor in repreh enderit in voluptate esse cillum dolorea.</p>
  <p class="abs about-text" style="top:1983px">Lorem ipsum dolor sit amet, consectetur adipiscing elit, sed do eiusmod tempor incididunt ut labore et dolore magna aliqua. Ut enim ad minim veniam, quis nostrud.</p>
  <div class="btn" style="left:618px;top:2095px;width:148px;height:48px">Lees verder
    <svg class="arrow" viewBox="0 0 12 12"><circle cx="6" cy="6" r="6" fill="#fff"/><path d="M5 3.5 7.5 6 5 8.5" stroke="#29a3df" stroke-width="1.6" fill="none"/></svg>
  </div>
</section>

<!-- Testimonials -->
<section>
  <h2 class="h2" style="top:2377px"><b>GETUIGENISSEN</b></h2>
  <svg class="divider" style="top:2428px" viewBox="0 0 130 20"><path d="M0 10H57M73 10H130" stroke="#6f87ab" stroke-width="1.5"/><circle cx="65" cy="10" r="7" fill="none" stroke="#6f87ab" stroke-width="1.5"/><circle cx="65" cy="10" r="2.5" fill="#29a3df"/></svg>

  <div class="t-card" style="left:111px">
    <div class="t-avatar" role="img" aria-label="Portrait photo of the reviewer"></div>
    <div class="t-name">Sanne de Vries</div><div class="t-stars">★★★★★</div>
    <p class="t-text">Lorem ipsum dolor sit amet, consectetur adipiscing elit, sed do eiusmod tempor incididunt ut labore et dolore magna aliqua. Ut enim ad minim veniam, quis nostrud exercitation ullamco.</p>
  </div>
  <div class="t-card" style="left:447px">
    <div class="t-avatar" role="img" aria-label="Portrait photo of the reviewer"></div>
    <div class="t-name">Pieter Bakker</div><div class="t-stars">★★★★★</div>
    <p class="t-text">Lorem ipsum dolor sit amet, consectetur adipiscing elit, sed do eiusmod tempor incididunt ut labore et dolore magna aliqua. Ut enim ad minim veniam, quis nostrud exercitation ullamco.</p>
  </div>
  <div class="t-card" style="left:782px">
    <div class="t-avatar" role="img" aria-label="Portrait photo of the reviewer"></div>
    <div class="t-name">Lotte Jansen</div><div class="t-stars">★★★★★</div>
    <p class="t-text">Lorem ipsum dolor sit amet, consectetur adipiscing elit, sed do eiusmod tempor incididunt ut labore et dolore magna aliqua. Ut enim ad minim veniam, quis nostrud exercitation ullamco.</p>
  </div>

  <svg class="t-arrow" style="left:43px" viewBox="0 0 34 34"><circle cx="17" cy="17" r="17" fill="#dbeaf5"/><path d="M19 11 13 17 19 23" stroke="#29a3df" stroke-width="2" fill="none"/></svg>
  <svg class="t-arrow" style="left:1122px" viewBox="0 0 34 34"><circle cx="17" cy="17" r="17" fill="#29a3df"/><path d="M15 11 21 17 15 23" stroke="#fff" stroke-width="2" fill="none"/></svg>
</section>

<!-- Contact -->
<section>
  <h2 class="h2" style="top:3037px"><b>NEEM CONTACT</b> <span>MET ONS OP</span></h2>
  <svg class="divider" style="top:3087px" viewBox="0 0 130 20"><path d="M0 10H57M73 10H130" stroke="#6f87ab" stroke-width="1.5"/><circle cx="65" cy="10" r="7" fill="none" stroke="#6f87ab" stroke-width="1.5"/><circle cx="65" cy="10" r="2.5" fill="#29a3df"/></svg>
  <div class="field" style="left:165px;top:3146px;width:283px;height:49px">Voor-en achternaam</div>
  <div class="field" style="left:459px;top:3146px;width:282px;height:49px">Telefoonnummer</div>
  <div class="field" style="left:752px;top:3146px;width:283px;height:49px">E-mailadres</div>
  <div class="field" style="left:165px;top:3207px;width:870px;height:95px">Bericht...!</div>
  <div class="btn" style="left:502px;top:3318px;width:196px;height:48px;font-size:14px">Bericht versturen</div>
</section>

<!-- Footer -->
<footer>
  <svg class="abs" style="left:0;top:3431px" width="1200" height="200" viewBox="0 0 1200 200">
    <path d="M0 55C150 130 300 135 450 90C600 40 700 5 830 5L830 200L0 200Z" fill="#29a3df"/>
    <path d="M0 150C250 150 480 30 720 12C950 0 1100 70 1200 140L1200 200L0 200Z" fill="#1b1c1e"/>
  </svg>
  <div class="footer-base"></div>

  <div class="abs logo-name" style="left:111px;top:3715px;color:#29a3df"><span class="logo-dot"></span>Zvo Klinieken</div>

  <div class="f-head" style="left:390px">Navigatie</div><div class="f-line" style="left:390px"></div>
  <div class="f-item" style="left:391px;top:3662px"><i></i>Home</div>
  <div class="f-item" style="left:391px;top:3703px"><i></i>Over Ons</div>
  <div class="f-item" style="left:391px;top:3743px"><i></i>Behandelingen</div>
  <div class="f-item" style="left:391px;top:3784px"><i></i>De Praktijk</div>
  <div class="f-item" style="left:391px;top:3825px"><i></i>Contact</div>

  <div class="f-head" style="left:592px">Snelle koppelingen</div><div class="f-line" style="left:592px"></div>
  <div class="f-item" style="left:593px;top:3662px"><i></i>Sitemap</div>
  <div class="f-item" style="left:593px;top:3703px"><i></i>Privacybeleid</div>
  <div class="f-item" style="left:593px;top:3743px"><i></i>Gebruiksvoorwaarden</div>
  <div class="f-item" style="left:593px;top:3784px"><i></i>Juridische ondersteuning</div>

  <div class="f-head" style="left:851px">Contact informatie</div><div class="f-line" style="left:851px"></div>
  <svg class="f-icon" style="top:3664px" width="10" height="14" viewBox="0 0 10 14"><path d="M5 0a5 5 0 0 1 5 5c0 4-5 9-5 9S0 9 0 5a5 5 0 0 1 5-5z" fill="#29a3df"/><circle cx="5" cy="5" r="1.8" fill="#1b1c1e"/></svg>
  <div class="f-contact" style="top:3660px"><b>ADRES:</b><br>Veldlaan 27, 2715 KL<br>Zoetermeer</div>
  <svg class="f-icon" style="top:3737px" width="12" height="12" viewBox="0 0 12 12"><path d="M2 .5c.5-.5 1.3-.5 1.6 0l1.2 2c.2.4 0 .9-.3 1.2l-.7.5c.6 1.3 1.6 2.3 2.9 2.9l.5-.7c.3-.4.8-.5 1.2-.3l2 1.2c.5.3.5 1.1 0 1.6l-.8.8c-.8.8-2 .9-3 .3C4.2 8.7 2.3 6.8 1 4.3.5 3.3.6 2.1 1.4 1.3z" fill="#29a3df"/></svg>
  <div class="f-contact" style="top:3734px"><b>TELEFOON:</b><br>+31 (79) 555 0142</div>
  <svg class="f-icon" style="top:3792px" width="13" height="10" viewBox="0 0 13 10"><rect width="13" height="10" rx="1" fill="#29a3df"/><path d="M0 1 6.5 6 13 1" stroke="#1b1c1e" stroke-width="1.2" fill="none"/></svg>
  <div class="f-contact" style="top:3789px"><b>E-MAIL:</b><br>info@zvoklinieken.nl</div>

  <div class="abs" style="left:111px;top:3870px;width:978px;height:1px;background:#3a3b3e"></div>
  <div class="abs" style="left:395px;top:3888px;font-size:13.5px;color:#e6e6e6">© 2023 <b style="color:#fff;font-weight:700">ZVO KLINIEKEN ZOETERMEER</b> &nbsp;| &nbsp;Alle rechten voorbehouden</div>
  <span class="social" style="left:975px"></span>
  <span class="social" style="left:1015px"></span>
  <span class="social" style="left:1056px"></span>
</footer>

</body>
</html>
```